Velutra Showcases | Web Design Project

We need a web design for a new Promotion Company based in Toronto, Canada named Velutra Showcases.

Velutra Showcases has an idea and vision to set high standard, be EXCLUSIVE and attract a group of people that will follow us through events we promote (night clubs, brand promotions, music events, and sport events)

We want to present a high standards and classy image to the others...

layout/style of the website would be best explained by this template

http://www.gorvikdesigns.example/view-ttemplate-58174.html

Target Market(s)

male/female age 25-40 Target: business owners young entrepreneur - clubing industry - media industry - promotion industry - marketing media industry

Industry/Entity Type

It Company

Requirements
Must have
• website would have about 5 pages ... example in terms of content (http://www.brastonhouse.example/lifestyle.html)

About Velutra
Events
Media
Promotions
Affiliates
Contact

as well as twitter and facebook logo/links
newsletter section
music control

need to have a easy to view gallery page (pictures from events)
Events would have to include flyers .. for past/future events
Media - would include videos/pictures from the events

Affiliates - list of affiliates with their logos and short description..

Main Pages
background would be pictures of Toronto
it would be nice to have some kind of flash/swf
space for flyer and picture of the week...

logo file is uploaded.

```html
<!DOCTYPE html>
<html lang="en">
<head>
<meta charset="utf-8">
<title>Velutra Showcases — Contact</title>
<link rel="stylesheet" href="https://fonts.googleapis.com/css2?family=Questrial&display=swap">
<style>
  :root {
    --ink: #ffffff;
    --accent: #2ea7df;
    --bar: rgba(0, 0, 0, 0.82);
    --panel: rgba(0, 0, 0, 0.86);
    --card: rgba(40, 40, 40, 0.55);
    --field: #121212;
    --rule: #8a8a8a;
    --sky-top: #5a7fa8;
    --sky-mid: #8f8a86;
    --city-low: #2b2622;
    --city-glow: #8a5a32;
  }
  * { box-sizing: border-box; margin: 0; padding: 0; }
  html, body { width: 1200px; height: 750px; overflow: hidden; background: #000; }
  body { position: relative; font-family: "Questrial", sans-serif; color: var(--ink); }

  .city-backdrop {
    position: absolute; inset: 0;
    background:
      radial-gradient(ellipse 320px 260px at 1010px 600px, rgba(214, 140, 70, 0.55), transparent 70%),
      linear-gradient(180deg, var(--sky-top) 0%, #7d92ab 22%, var(--sky-mid) 40%, #4a4440 60%, var(--city-low) 100%);
  }
  .backdrop-band {
    position: absolute; top: 0; bottom: 0; left: 200px; width: 600px;
    background: rgba(0, 0, 0, 0.25);
  }
  .backdrop-band.right { left: 800px; width: 200px; background: rgba(0, 0, 0, 0.1); }

  /* top bar */
  .top-bar {
    position: absolute; left: 0; top: 0; width: 1200px; height: 28px;
    background: var(--bar);
  }
  .nav-home { position: absolute; left: 9px; top: 5px; }
  .nav-link {
    position: absolute; top: 0; height: 28px; line-height: 29px;
    font-size: 18.5px; letter-spacing: 0.2px; color: var(--ink); text-decoration: none;
  }
  .nav-link.current { background: #2a2a2a; left: 37px !important; width: 163px; padding-left: 10px; }
  .player-controls { position: absolute; left: 912px; top: 9px; display: flex; gap: 11px; }
  .now-playing {
    position: absolute; left: 1000px; top: 0; width: 200px; height: 28px;
    background: #000; font-size: 11px; line-height: 29px; padding-left: 5px;
    white-space: nowrap; overflow: hidden;
  }

  /* main panel */
  .content-panel {
    position: absolute; left: 225px; top: 47px; width: 750px; height: 656px;
    background: var(--panel);
  }
  .gallery { position: absolute; left: 94px; top: 15px; width: 562px; height: 214px; background: #000; }
  .gallery-photo { position: absolute; }

  .intro-text {
    position: absolute; left: 94px; top: 251px; width: 562px; overflow: hidden;
    font-size: 10.4px; line-height: 13.4px; letter-spacing: 0.05px;
  }
  .intro-text p { white-space: nowrap; }

  .contact-card {
    position: absolute; left: 94px; top: 326px; width: 562px; height: 316px;
    background: var(--card);
  }
  .contact-details { position: absolute; left: 23px; top: 11px; width: 200px; font-size: 11.4px; line-height: 13.2px; text-transform: uppercase; }
  .brand-name { font-size: 29px; line-height: 32px; color: var(--accent); letter-spacing: 0.5px; }
  .company-heading { color: var(--accent); font-size: 13.5px; margin: 14px 0 16px; }
  .contact-details .group { margin-bottom: 13px; }
  .contact-details .email { font-size: 9px; color: var(--accent); }
  .contact-details .email span { color: var(--ink); font-size: 11.4px; }
  .column-rule { position: absolute; left: 238px; top: 19px; width: 2px; height: 278px; background: var(--rule); }

  .form-label { position: absolute; left: 276px; font-size: 13.5px; color: var(--accent); }
  .form-field { position: absolute; left: 352px; width: 187px; height: 18px; background: var(--field); }
  .form-field.select { font-size: 8.5px; line-height: 18px; padding-left: 7px; background: #0c0c0c; }
  .form-field.select svg { position: absolute; right: 6px; top: 6px; }
  .form-field.message { height: 118px; }
  .submit-button {
    position: absolute; left: 489px; top: 252px; width: 50px; height: 15px;
    background: var(--accent); font-size: 8px; line-height: 15px; text-align: center;
  }

  /* footer */
  .site-footer {
    position: absolute; left: 0; top: 722px; width: 1200px; height: 28px;
    background: var(--bar); font-size: 14px; line-height: 29px; padding-left: 9px;
  }
  .site-footer a { color: var(--accent); text-decoration: none; }
  .social-links { position: absolute; right: 10px; top: 7px; display: flex; gap: 9px; }
  .social-links span { width: 15px; height: 15px; border-radius: 2px; display: block; }
</style>
</head>
<body>
  <div class="city-backdrop" role="img" aria-label="Evening skyline photograph of downtown Toronto"></div>
  <div class="backdrop-band"></div>
  <div class="backdrop-band right"></div>

  <header class="top-bar">
    <svg class="nav-home" width="17" height="15" viewBox="0 0 17 15" aria-label="Home">
      <path d="M8.5 0 L17 7.5 H14.5 V15 H10.5 V10 H6.5 V15 H2.5 V7.5 H0 Z" fill="#2ea7df"/>
    </svg>
    <a class="nav-link current">ABOUT VELUTRA</a>
    <a class="nav-link" style="left:211px">MEDIA</a>
    <a class="nav-link" style="left:286px">EVENTS</a>
    <a class="nav-link" style="left:368px">PROMOTIONS</a>
    <a class="nav-link" style="left:501px">AFFILIATES</a>
    <a class="nav-link" style="left:605px">CONTACT</a>

    <div class="player-controls" aria-label="Music controls">
      <svg width="10" height="10" viewBox="0 0 10 10"><rect x="0" y="0" width="2" height="10" fill="#fff"/><path d="M10 0 V10 L2.5 5 Z" fill="#fff"/></svg>
      <svg width="10" height="10" viewBox="0 0 10 10"><path d="M2 0 V10 L9 5 Z" fill="#fff"/></svg>
      <svg width="10" height="10" viewBox="0 0 10 10"><path d="M0 0 V10 L7.5 5 Z" fill="#fff"/><rect x="8" y="0" width="2" height="10" fill="#fff"/></svg>
      <svg width="10" height="10" viewBox="0 0 10 10"><rect width="10" height="10" fill="#fff"/></svg>
    </div>
    <div class="now-playing">Nova Reyes; Midnight Signal (Radio Edit).....</div>
  </header>

  <main class="content-panel">
    <div class="gallery">
      <div class="gallery-photo" style="left:0;top:0;width:190px;height:77px;background:linear-gradient(180deg,#6d7480 0%,#3a4050 55%,#242a36 100%)" role="img" aria-label="Outdoor festival main stage under an evening sky"></div>
      <div class="gallery-photo" style="left:190px;top:0;width:181px;height:77px;background:radial-gradient(ellipse at 50% 20%,#c9b98a,#5a3a70 55%,#1e1530)" role="img" aria-label="Festival crowd under stage lights"></div>
      <div class="gallery-photo" style="left:371px;top:0;width:191px;height:214px;background:radial-gradient(ellipse at 45% 15%,#f4e9b0,#9a7a3a 35%,#3b2a1a 65%,#111 100%)" role="img" aria-label="DJ at the decks facing a lit-up crowd"></div>
      <div class="gallery-photo" style="left:13px;top:87px;width:161px;height:119px;background:linear-gradient(135deg,#f2a020 0%,#e0542a 50%,#b01f88 100%)" role="img" aria-label="Event flyer for Solstice Fields weekend festival"></div>
      <div class="gallery-photo" style="left:190px;top:77px;width:181px;height:137px;background:linear-gradient(160deg,#3a2a80 0%,#c43aa0 45%,#e8c040 70%,#111 100%)" role="img" aria-label="Crowd with raised hands beneath a neon festival banner"></div>
    </div>

    <div class="intro-text">
      <p>Lorem ipsum dolor sit amet, consetetur sadipscing elitr, sed diam nonumy eirmod tempor invidunt ut labore et dolore magna aliquyam</p>
      <p>erat, sed diam voluptua. At vero eos et accusam et justo duo dolores et ea rebum. Stet clita kasd gubergren, no sea takimata sanctus</p>
      <p>Lorem ipsum dolor sit amet. Lorem ipsum dolor sit amet, consetetur sadipscing elitr,&nbsp; sed diam nonumy eirmod tempor invidunt ut labore</p>
      <p>et dolore magna aliquyam erat, sed diam voluptua. At vero eos et accusam et justo duo dolores et ea</p>
    </div>

    <section class="contact-card">
      <div class="contact-details">
        <div class="brand-name">VELUTRA</div>
        <div class="company-heading">VELUTRA SHOWCASES</div>
        <div class="group">48 Harlow Lane Suite 1204<br>Toronto, Ontario<br>M5X 0A9</div>
        <div class="group">T: 4160.5550.142<br>F: 4160.5550.143<br><span class="email"><span>E:</span>info@velutrashowcases.example</span></div>
        <div class="group">Adrian Holt<br>Director<br>T: 4160.5550.177<br><span class="email"><span>E:</span>adrian.holt@velutra.example</span></div>
        <div class="group">Daniel Moray<br>Co-Founder<br>T: 4160.5550.198<br><span class="email"><span>E:</span>daniel.moray@velutra.example</span></div>
      </div>
      <div class="column-rule"></div>

      <div class="form-label" style="top:31px">EVENT</div>
      <div class="form-label" style="top:64px">NAME</div>
      <div class="form-label" style="top:97px">EMAIL</div>
      <div class="form-label" style="top:130px">MESSAGE</div>

      <div class="form-field select" style="top:30px">SELECT YOUR EVENT
        <svg width="7" height="6" viewBox="0 0 7 6"><path d="M0 0 H7 L3.5 6 Z" fill="#fff"/></svg>
      </div>
      <div class="form-field" style="top:63px"></div>
      <div class="form-field" style="top:96px"></div>
      <div class="form-field message" style="top:129px"></div>
      <div class="submit-button">SUBMIT</div>
    </section>
  </main>

  <footer class="site-footer">
    COPYRIGHT © 2011 VELUTRA. USE OF THIS WEBSITE CONSTITUTES ACCEPTANCE OF OUR <a>USER AGREEMENT</a> AND <a>PRIVACY POLICY</a>.
    <div class="social-links">
      <span style="background:#e0782a" aria-label="News feed"></span>
      <span style="background:#4fa8d8" aria-label="Social link"></span>
      <span style="background:#3a5a98" aria-label="Social link"></span>
    </div>
  </footer>
</body>
</html>
```